Preferred pricing vendor

We are a plumbing company that has many services
-Boilers & Controls
-Plumbing & Heating
-HVAC & Refrigeration
-Preventative Maintenacne
-Gas fitting & Drain Cleaning

We primarily look after condo buildings, and our preferred service rates ($98, $93, or $88 depending on the contract) extend to all of our clients. So in essence, we look after the mechanical room and common equipment but our clients can call us in for drain cleaning or replacing a fixture in their suite. The discounted rates apply to the personal residence. We want a flyer to let them know they get a discount on our services. A one-pager we can send out to all of our contract clients.

Included source files for our letterhead and logo just so you can see the colours we go with.

Target Market(s)

Residential repairs, individual people, replacement of fixtures in-suite specific repairs

Requirements
Must have
• be colourful and attractive

```html
<!DOCTYPE html>
<html lang="en">
<head>
<meta charset="utf-8">
<title>Affordable Mechanical System Maintenance – Flyer</title>
<link href="https://fonts.googleapis.com/css2?family=Roboto:wght@400;700;900&display=swap" rel="stylesheet">
<style>
  :root {
    --backdrop: #8a8a8a;
    --navy: #1d4560;
    --navy-deep: #163649;
    --blue: #2a82c4;
    --blue-light: #3a9ae0;
    --orange: #e4643f;
    --paper: #ffffff;
    --pattern-grey: #ececec;
    --text-light: #ffffff;
  }
  * { box-sizing: border-box; margin: 0; padding: 0; }
  html, body {
    width: 1200px; height: 1082px; overflow: hidden;
    background: var(--backdrop);
    font-family: 'Roboto', sans-serif;
  }
  .flyer {
    position: absolute; left: 233px; top: 21px;
    width: 733px; height: 1039px;
    background: var(--paper);
    overflow: hidden;
  }
  .hero-photo {
    position: absolute; left: 0; top: 0; width: 100%; height: 531px;
    background: linear-gradient(160deg, #2c5a78 0%, var(--navy) 45%, var(--navy-deep) 100%);
  }
  .brand {
    position: absolute; top: 78px; left: 0; width: 100%;
    display: flex; justify-content: center; align-items: center; gap: 10px;
  }
  .brand-dot { width: 26px; height: 26px; border-radius: 50%; background: var(--orange); }
  .brand-name {
    font-weight: 900; font-size: 26px; color: var(--blue-light);
    letter-spacing: 0.5px; text-transform: uppercase;
  }
  .headline {
    position: absolute; top: 206px; left: 0; width: 100%;
    text-align: center; color: var(--text-light);
    font-weight: 700; font-size: 45px; line-height: 44px; letter-spacing: -0.5px;
  }
  .headline .accent { color: var(--blue-light); }
  .discount-band {
    position: absolute; left: 0; top: 531px; width: 100%; height: 131px;
    background: var(--pattern-grey);
  }
  .offer-badge {
    position: absolute; left: 219px; top: 368px; width: 294px; height: 294px;
    border-radius: 50%; background: var(--orange);
    color: var(--text-light); text-align: center;
  }
  .offer-badge .lead {
    margin-top: 50px; font-size: 23px; font-weight: 400; letter-spacing: 2.5px; line-height: 31px;
  }
  .offer-badge .rule { width: 72px; height: 4px; background: var(--text-light); margin: 16px auto 18px; }
  .offer-badge .main { font-size: 43px; font-weight: 700; line-height: 43px; }
  .services-intro {
    position: absolute; top: 696px; left: 40px; right: 40px;
    text-align: center; color: var(--orange);
    font-weight: 700; font-size: 27px; line-height: 34px; text-transform: uppercase;
  }
  .service-strip { position: absolute; left: 0; top: 873px; width: 100%; height: 166px; background: var(--blue); }
  .service {
    position: absolute; top: 832px; width: 120px; margin-left: -60px;
    text-align: center;
  }
  .service-icon {
    width: 82px; height: 82px; margin: 0 auto; border-radius: 50%;
    background: var(--paper); display: flex; align-items: center; justify-content: center;
  }
  .service-label {
    margin-top: 30px; color: var(--text-light);
    font-weight: 700; font-size: 14.5px; line-height: 22px; text-transform: uppercase;
  }
</style>
</head>
<body>
<main class="flyer">
  <div class="hero-photo" role="img" aria-label="Photo of a row of electrical switchgear cabinets in a mechanical room, tinted dark blue"></div>

  <div class="brand">
    <span class="brand-dot"></span>
    <span class="brand-name">Keystone Mechanical Inc</span>
  </div>

  <h1 class="headline">Affordable Mechanical<br>System <span class="accent">Maintenance</span></h1>

  <div class="discount-band" role="img" aria-label="Light grey background of repeated percent signs"></div>

  <div class="offer-badge">
    <p class="lead">BOOK NOW<br>TO GET</p>
    <div class="rule"></div>
    <p class="main">DISCOUNT<br>SERVICE</p>
  </div>

  <p class="services-intro">We offer full-service solutions for commercial and condo buildings in Calgary and Edmonton</p>

  <div class="service-strip"></div>

  <div class="service" style="left:81px">
    <div class="service-icon">
      <svg width="46" height="46" viewBox="0 0 46 46"><circle cx="23" cy="23" r="19" fill="none" stroke="#e4643f" stroke-width="4"/><path d="M15 31 L24 22 M22 16 l8 8 M26 12 v6 M34 20 h-6" stroke="#2a82c4" stroke-width="3.5" stroke-linecap="round"/></svg>
    </div>
    <p class="service-label">Electrical<br>Service</p>
  </div>
  <div class="service" style="left:194px">
    <div class="service-icon">
      <svg width="46" height="46" viewBox="0 0 46 46"><circle cx="23" cy="23" r="19" fill="none" stroke="#e4643f" stroke-width="4"/><path d="M16 26c-3-4 2-7 0-11 4 3 3 7 0 11zM23 26c-3-4 2-7 0-11 4 3 3 7 0 11zM30 26c-3-4 2-7 0-11 4 3 3 7 0 11z" fill="#e4643f"/><rect x="13" y="28" width="20" height="4" rx="2" fill="#2a82c4"/></svg>
    </div>
    <p class="service-label">Gas Fitting &amp;<br>Drain Cleaning</p>
  </div>
  <div class="service" style="left:309px">
    <div class="service-icon">
      <svg width="46" height="46" viewBox="0 0 46 46"><circle cx="23" cy="23" r="19" fill="none" stroke="#e4643f" stroke-width="4"/><path d="M23 11c5 7 8 11 8 15a8 8 0 0 1-16 0c0-4 3-8 8-15z" fill="#2a82c4"/></svg>
    </div>
    <p class="service-label">Plambing<br>Service</p>
  </div>
  <div class="service" style="left:422px">
    <div class="service-icon">
      <svg width="46" height="46" viewBox="0 0 46 46"><circle cx="23" cy="23" r="19" fill="none" stroke="#e4643f" stroke-width="4"/><path d="M17 13c-3 4 3 7 0 11s3 7 0 9M23 13c-3 4 3 7 0 11s3 7 0 9M29 13c-3 4 3 7 0 11s3 7 0 9" fill="none" stroke="#2a82c4" stroke-width="2.8" stroke-linecap="round"/></svg>
    </div>
    <p class="service-label">Boilers &amp;<br>Controls</p>
  </div>
  <div class="service" style="left:532px">
    <div class="service-icon">
      <svg width="46" height="46" viewBox="0 0 46 46"><circle cx="23" cy="23" r="19" fill="none" stroke="#e4643f" stroke-width="4"/><path d="M23 11c6 6 9 10 9 15a9 9 0 0 1-18 0c0-4 2-6 4-8 0 3 1 5 3 5-1-5 0-8 2-12z" fill="#2a82c4"/></svg>
    </div>
    <p class="service-label">Heating<br>Service</p>
  </div>
  <div class="service" style="left:648px">
    <div class="service-icon">
      <svg width="46" height="46" viewBox="0 0 46 46"><circle cx="23" cy="23" r="19" fill="none" stroke="#e4643f" stroke-width="4"/><circle cx="23" cy="23" r="12" fill="#2a82c4"/><path d="M23 23v-9M23 23l8 5M23 23l-8 5" stroke="#fff" stroke-width="2.5" stroke-linecap="round"/><circle cx="23" cy="23" r="2.5" fill="#fff"/></svg>
    </div>
    <p class="service-label">HVAC &amp;<br>Refrigeration</p>
  </div>
</main>
</body>
</html>
```